Small Business Broker Business Card Design

A business card design for a small business brokerage, which is a financial service, not unlike real estate brokerage, but for small businesses such as laundromats, pizza shops, restaurants, cleaners etc. The designs should all be simple, more conservative in nature, using the colors and font of the logo. Again, think real estate Brokerage as a business context
Contact Information for Business Card
Name: Glen R. Harlow. Title: Small Business Advisor. Email: g.harlow@bayfieldcapitalworks.example. Mobile: (555) 274-3918. Office: (555) 806-2147. www.bayfieldcapitalworks.example

```html
<!DOCTYPE html>
<html lang="en">
<head>
<meta charset="utf-8">
<title>Bayfield Capital Works – Business Card</title>
<link rel="stylesheet" href="https://fonts.googleapis.com/css2?family=Montserrat:wght@500;600;700&family=Arimo:wght@400&display=swap">
<style>
  :root {
    --navy: #163a6c;
    --navy-light: #24497c;
    --green: #8cc63f;
    --white: #ffffff;
    --backdrop: #e9e9ec;
  }
  * { box-sizing: border-box; margin: 0; padding: 0; }
  html, body { width: 1200px; height: 716px; overflow: hidden; }
  body {
    background: var(--backdrop);
    display: flex;
    align-items: center;
    justify-content: center;
    gap: 30px;
  }
  .card {
    width: 560px;
    height: 320px;
    background: var(--navy);
    position: relative;
    overflow: hidden;
    color: var(--white);
  }
  .card--back {
    background: linear-gradient(135deg, var(--navy-light) 0%, var(--navy) 55%);
  }

  /* brand block */
  .brand {
    display: flex;
    flex-direction: column;
    align-items: center;
    text-align: center;
  }
  .brand__mark {
    width: 46px;
    height: 46px;
    border-radius: 50%;
    background: var(--green);
    margin-bottom: 16px;
  }
  .brand__name {
    font-family: "Montserrat", sans-serif;
    font-weight: 600;
    font-size: 19px;
    letter-spacing: 0.5px;
    text-transform: uppercase;
    color: var(--white);
    white-space: nowrap;
  }
  .brand__tagline {
    font-family: "Montserrat", sans-serif;
    font-weight: 500;
    font-size: 10.5px;
    letter-spacing: 1.4px;
    text-transform: uppercase;
    color: var(--green);
    margin-top: 4px;
    white-space: nowrap;
  }
  .card--front .brand {
    position: absolute;
    inset: 0;
    justify-content: center;
  }

  /* back side */
  .card--back .brand {
    position: absolute;
    left: 22px;
    top: 100px;
    width: 240px;
  }
  .card--back .brand__mark { width: 30px; height: 30px; margin-bottom: 10px; }
  .card--back .brand__name { font-size: 12px; letter-spacing: 0.2px; }
  .card--back .brand__tagline { font-size: 6.6px; letter-spacing: 0.8px; margin-top: 3px; }

  .divider {
    position: absolute;
    left: 278px;
    top: 90px;
    width: 1px;
    height: 140px;
    background: var(--green);
  }
  .contact {
    position: absolute;
    left: 296px;
    top: 92px;
  }
  .contact__name {
    font-family: "Montserrat", sans-serif;
    font-weight: 700;
    font-size: 20px;
    text-transform: uppercase;
    color: var(--green);
    letter-spacing: 0.3px;
  }
  .contact__title {
    font-family: "Arimo", sans-serif;
    font-size: 13px;
    color: var(--white);
    margin-bottom: 14px;
  }
  .contact__list { list-style: none; }
  .contact__item {
    display: flex;
    align-items: center;
    gap: 8px;
    font-family: "Arimo", sans-serif;
    font-size: 12.5px;
    line-height: 20px;
    color: var(--white);
  }
  .contact__icon { width: 11px; height: 11px; flex: none; }
</style>
</head>
<body>

<section class="card card--front" aria-label="Card front">
  <div class="brand">
    <span class="brand__mark"></span>
    <p class="brand__name">Bayfield Capital Works, Inc</p>
    <p class="brand__tagline">Trusted guidance for every small business sale</p>
  </div>
</section>

<section class="card card--back" aria-label="Card back">
  <div class="brand">
    <span class="brand__mark"></span>
    <p class="brand__name">Bayfield Capital Works, Inc</p>
    <p class="brand__tagline">Trusted guidance for every small business sale</p>
  </div>

  <span class="divider"></span>

  <div class="contact">
    <h1 class="contact__name">Glen R. Harlow</h1>
    <p class="contact__title">Small Business Advisor</p>
    <ul class="contact__list">
      <li class="contact__item">
        <svg class="contact__icon" viewBox="0 0 12 12" aria-hidden="true"><path fill="#8cc63f" d="M1 4c0-2 2-3 5-3s5 1 5 3l-2 1-1-1.5H4L3 5zM3 6h6l1 5H2z"/></svg>
        (555) 806-2147
      </li>
      <li class="contact__item">
        <svg class="contact__icon" viewBox="0 0 12 12" aria-hidden="true"><rect x="3" y="0.5" width="6" height="11" rx="1" fill="none" stroke="#8cc63f" stroke-width="1.2"/><circle cx="6" cy="9.5" r="0.7" fill="#8cc63f"/></svg>
        (555) 274-3918
      </li>
      <li class="contact__item">
        <svg class="contact__icon" viewBox="0 0 12 12" aria-hidden="true"><rect x="0.5" y="2.5" width="11" height="7.5" fill="#8cc63f"/><path d="M0.5 2.5 6 7l5.5-4.5" fill="none" stroke="#163a6c" stroke-width="1"/></svg>
        g.harlow@bayfieldcapitalworks.example
      </li>
      <li class="contact__item">
        <svg class="contact__icon" viewBox="0 0 12 12" aria-hidden="true"><circle cx="6" cy="6" r="5.2" fill="none" stroke="#8cc63f" stroke-width="1.2"/><path d="M1 6h10M6 1c-2.5 3-2.5 7 0 10M6 1c2.5 3 2.5 7 0 10" fill="none" stroke="#8cc63f" stroke-width="0.9"/></svg>
        www.bayfieldcapitalworks.example
      </li>
    </ul>
  </div>
</section>

</body>
</html>
```